Talvex Health Artificial Intelligence MedTech Software Website Refresh

We need a new website (old one at www.talvex-health.example is no longer relevant) for our medtech software company using artificial intelligence to deliver higher quality, faster and more cost effective care in oncology. The audiences are both healthcare providers and health insurance payers. We've created an extensive outline to follow and have the old site still live for easy content use and repurposing. Our primary need is a great overhaul to look and feel. If we find a successful designer, we will need additional work done for graphics and other presentation projects.

Target Market(s)

Health care providers (doctors) and administrators plus health insurers

Industry/Entity Type

Medtech

Coding

Number of Pages Required

5+ page

Font styles to use
Other font styles liked:
• Roboto see Style Guide

Requirements
Must have
• See attached brief
Nice to have
• See attached brief. We like www.caremint.example and www.lumoradx.example as sites.
Should not have
• See attached brief

```html
<!DOCTYPE html>
<html lang="en">
<head>
<meta charset="utf-8">
<title>Talvex Health</title>
<link href="https://fonts.googleapis.com/css2?family=Roboto:wght@300;400;500;700;900&display=swap" rel="stylesheet">
<style>
:root{
  --blue:#1e73c8;
  --blue-dark:#0d4a9e;
  --blue-light:#2c9ddc;
  --navy:#0b2f7a;
  --ink:#111;
  --muted:#666;
  --gray-bg:#f2f2f2;
  --white:#fff;
}
*{box-sizing:border-box;margin:0;padding:0}
html,body{width:1200px;height:3446px;overflow:hidden}
body{font-family:'Roboto',sans-serif;color:var(--ink);background:var(--white);position:relative}
.abs{position:absolute}
.hero{left:0;top:0;width:1200px;height:654px;background:linear-gradient(100deg,#1f62bf 0%,#1f7cd0 55%,#2a9de0 100%)}
.logo{display:flex;align-items:center;gap:10px;font-weight:700;font-size:40px;letter-spacing:-.5px}
.logo .dot{width:22px;height:22px;border-radius:50%}
.hero .logo{left:110px;top:38px;color:var(--white)}
.hero .logo .dot{background:#5fc3f0}
.nav{right:110px;top:60px;display:flex;gap:27px;font-size:14.5px;font-weight:500;color:var(--white)}
.nav .active{color:#5fc3f0;border-bottom:3px solid #5fc3f0;padding-bottom:6px}
.hero h1{left:110px;top:196px;font-size:50px;font-weight:700;color:var(--white)}
.hero .lead{left:110px;top:268px;width:500px;font-size:15px;font-weight:500;line-height:24px;color:var(--white)}
.hero ul{left:110px;top:355px;width:495px;list-style:none;color:var(--white);font-size:13px;line-height:21.5px;font-weight:300}
.hero li{position:relative;padding-left:26px;margin-bottom:15px}
.hero li svg{position:absolute;left:0;top:3px}
.photo{border-radius:50%;width:140px;height:140px;border:3px solid rgba(255,255,255,.6)}
.section-title{left:0;width:1200px;text-align:center;font-size:38px;font-weight:700;color:var(--ink)}
.section-title span{color:var(--blue)}
.intro{left:190px;top:822px;width:820px;text-align:center;font-size:13.5px;line-height:25.5px;color:var(--muted);font-weight:300}
.metric{width:310px;height:310px;border-radius:50%;color:var(--white);display:flex;flex-direction:column;align-items:center;justify-content:center;text-align:center}
.metric .big{font-size:38px;font-weight:700;line-height:42px}
.metric .sub{font-size:23px;font-weight:500;margin-top:12px;line-height:28px}
.feature{width:240px;text-align:center}
.feature .ico{width:100px;height:100px;border-radius:50%;background:#efefef;margin:0 auto;display:flex;align-items:center;justify-content:center}
.feature h3{font-size:17.5px;font-weight:500;margin-top:22px}
.feature p{font-size:13.5px;line-height:21.5px;color:var(--muted);margin-top:14px;font-weight:300}
.card{width:313px;height:363px;background:var(--white);border:1px solid #ddd}
.card .img{height:207px}
.card h4{font-size:16.5px;font-weight:500;line-height:22px;margin:22px 22px 0}
.card .meta{font-size:12.5px;color:#999;margin:12px 22px 0;padding-bottom:12px;border-bottom:1px solid #e3e3e3}
.card .dl{font-size:14.5px;color:var(--blue);font-weight:500;margin:16px 22px 0;display:flex;gap:8px;align-items:center}
.partner{width:235px;height:113px;background:var(--white);box-shadow:0 2px 8px rgba(0,0,0,.12);display:flex;align-items:center;justify-content:center}
.partner .badge{width:150px;height:36px;border-radius:4px}
.contact{left:0;top:2753px;width:1200px;height:319px;background:var(--blue)}
.contact h2{position:absolute;top:50px;width:1200px;text-align:center;color:var(--white);font-size:38px;font-weight:500}
.c-item{position:absolute;top:125px;width:260px;text-align:center;color:var(--white)}
.c-item .ico{width:54px;height:54px;border-radius:50%;background:#2aa0e4;margin:0 auto;display:flex;align-items:center;justify-content:center}
.c-item h5{font-size:15.5px;font-weight:500;margin-top:17px}
.c-item p{font-size:13.5px;line-height:21px;margin-top:8px;font-weight:300}
.footer .logo{left:110px;top:3160px;color:var(--blue)}
.footer .logo .dot{background:var(--blue-light)}
.socials{left:123px;top:3270px;display:flex;gap:8px}
.socials span{width:35px;height:35px;border-radius:50%;border:1px solid #555;display:block}
.fcol h6{font-size:16px;font-weight:500;margin-bottom:14px}
.fcol a{display:block;font-size:13px;color:#555;line-height:26px;text-decoration:none}
.finfo{font-size:13px;color:#444;line-height:19px;padding-left:22px;position:relative;margin-bottom:14px}
.finfo b{font-size:11.5px;font-weight:500;color:var(--ink);display:block}
.finfo svg{position:absolute;left:0;top:2px}
.divider{left:110px;top:3373px;width:980px;height:1px;background:#ddd}
.copy{left:0;top:3393px;width:1200px;text-align:center;font-size:13px;color:#555}
</style>
</head>
<body>

<section class="hero abs">
  <div class="logo abs">Talvex Health <span class="dot"></span></div>
  <nav class="nav abs"><span class="active">Home</span><span>Solutions</span><span>Clinical Evidence</span><span>About</span><span>Contact Us</span></nav>
  <h1 class="abs">TALVEX HEALTH, INC.</h1>
  <p class="lead abs">Talvex Health, Inc. is an expert team with the vision of improving oncology treatment delivery, patient outcomes and cost effectiveness through the power of AI.</p>
  <ul class="abs">
    <li><svg width="13" height="13" viewBox="0 0 13 13"><circle cx="6.5" cy="6.5" r="6.5" fill="#fff"/><path d="M3.5 6.7l2 2 4-4" stroke="#1f70c9" stroke-width="1.6" fill="none"/></svg>The problem(s) for providers: creating a treatment directive starts from scratch for every patient and is a time consuming iterative/back and forth process . Further, because there is little transparency to communicate patient-specific treatment needs to the payer, prior authorization is a burden.</li>
    <li><svg width="13" height="13" viewBox="0 0 13 13"><circle cx="6.5" cy="6.5" r="6.5" fill="#fff"/><path d="M3.5 6.7l2 2 4-4" stroke="#1f70c9" stroke-width="1.6" fill="none"/></svg>The problem for payers: there is no transparency to the uniqueness of the patient<br>so the process has costly delays to gather more information and align the treatment to what's best for the patient; often attempts to redirect care are</li>
  </ul>
  <div class="photo abs" style="left:835px;top:135px;background:radial-gradient(circle at 50% 55%,#e9c3a8,#b9a89a)" role="img" aria-label="Portrait photo of a patient wearing a headscarf"></div>
  <div class="photo abs" style="left:667px;top:303px;background:radial-gradient(circle,#f1ece8,#c9b4a6)" role="img" aria-label="Photo of a clinician's hands in a white coat"></div>
  <div class="photo abs" style="left:835px;top:303px;background:radial-gradient(circle,#9a9a9a,#6e6e6e)" role="img" aria-label="Photo of a patient in a gray shirt"></div>
  <div class="photo abs" style="left:1002px;top:303px;background:radial-gradient(circle,#dbe6ee,#a9bccb)" role="img" aria-label="Photo of a clinic interior"></div>
  <div class="photo abs" style="left:835px;top:470px;background:radial-gradient(circle,#f3efea,#cfb29b)" role="img" aria-label="Photo of hands holding a patient's arm"></div>
</section>

<h2 class="section-title abs" style="top:748px">OUR <span>SOLUTIONS</span></h2>
<p class="intro abs">Talvex Health improves cancer therapy through AI-powered analysis and comparison of over 10 million clinical images and over 30,000 patient datasets.Our commercially available, FDA-cleared software suite uses AI to match each new patient to a massive, proprietary, expert database in order to precisely tailor treatment to each patient's unique characteristics, and align the treatment directive between the payer and provider to what's best for the patient.</p>

<svg class="abs" style="left:110px;top:972px" width="980" height="378" viewBox="0 0 980 378">
  <circle cx="189" cy="189" r="185" fill="none" stroke="#2a8ed6" stroke-width="6"/>
  <circle cx="490" cy="189" r="185" fill="#fff" stroke="#2a8ed6" stroke-width="6"/>
  <circle cx="789" cy="189" r="185" fill="#fff" stroke="#2a8ed6" stroke-width="6"/>
  <circle cx="189" cy="189" r="182" fill="#fff" stroke="none"/>
  <path d="M189 4 A185 185 0 0 0 189 374" fill="none" stroke="#2a8ed6" stroke-width="6"/>
</svg>
<div class="metric abs" style="left:144px;top:1006px;background:linear-gradient(180deg,#1c63b8,#0d2f82)">
  <svg width="90" height="80" viewBox="0 0 90 80" fill="none" stroke="#fff" stroke-width="2.5"><circle cx="50" cy="20" r="14"/><path d="M50 12v16M46 16h7a3 3 0 010 6h-6a3 3 0 000 6h7"/><path d="M10 65l14-14c4-4 10-5 14-2l8 6h16a4 4 0 010 8H45M20 72l8-8h22l24-14a4 4 0 014 6L54 74H30"/></svg>
  <div class="big" style="margin-top:12px">$15M<br>PMPY</div><div class="sub">Payer</div>
</div>
<div class="metric abs" style="left:445px;top:1006px;background:linear-gradient(180deg,#33b1e6,#1a6fcc)">
  <svg width="80" height="80" viewBox="0 0 80 80" fill="none" stroke="#fff" stroke-width="2.5"><circle cx="34" cy="24" r="14"/><path d="M8 70c0-16 12-26 26-26 6 0 10 1 14 4"/><circle cx="58" cy="58" r="14"/><path d="M58 50v16M50 58h16"/></svg>
  <div class="big" style="margin-top:18px">Patient</div><div class="sub">30% reduction in<br>side efforts</div>
</div>
<div class="metric abs" style="left:744px;top:1006px;background:linear-gradient(180deg,#1c63b8,#0d2f82)">
  <svg width="90" height="80" viewBox="0 0 90 80" fill="none" stroke="#fff" stroke-width="2.5"><path d="M22 50a14 14 0 010-28 22 22 0 0146 0 14 14 0 010 28"/><circle cx="45" cy="32" r="10"/><circle cx="45" cy="62" r="10"/><circle cx="45" cy="62" r="4"/></svg>
  <div class="big" style="margin-top:12px">$4k/<br>Patient</div><div class="sub">Provider</div>
</div>

<div class="feature abs" style="left:78px;top:1402px"><div class="ico"><svg width="52" height="52" viewBox="0 0 52 52" fill="none" stroke="#1e73c8" stroke-width="2"><rect x="4" y="4" width="12" height="12"/><rect x="36" y="4" width="12" height="12"/><rect x="4" y="36" width="12" height="12"/><rect x="36" y="36" width="12" height="12"/><rect x="19" y="19" width="14" height="14"/><path d="M16 10h10v9M36 42H26v-9M10 16v10h9M42 36V26h-9"/></svg></div><h3>Integrated</h3><p>Integrated into MD clinical workflows and IT systems</p></div>
<div class="feature abs" style="left:339px;top:1402px"><div class="ico"><svg width="52" height="52" viewBox="0 0 52 52" fill="none" stroke="#1e73c8" stroke-width="2"><path d="M14 46V34c-6-4-8-10-6-17C11 8 20 4 28 5c9 1 15 8 15 17l4 8h-5v8h-8v8"/><rect x="18" y="14" width="14" height="14"/><path d="M21 14v-3M29 14v-3M21 28v3M29 28v3M18 18h-3M18 24h-3M32 18h3M32 24h3"/></svg></div><h3>Automated PA</h3><p>Automated PA removing manual processes, saving administrative costs</p></div>
<div class="feature abs" style="left:601px;top:1402px"><div class="ico"><svg width="52" height="52" viewBox="0 0 52 52" fill="none" stroke="#1e73c8" stroke-width="2"><rect x="8" y="8" width="36" height="30"/><path d="M4 42h44v4H4zM14 32V22M22 32V16M30 32V24M38 14l-6 6"/></svg></div><h3>Improved care quality</h3><p>Improved care quality equal or better personalized care</p></div>
<div class="feature abs" style="left:863px;top:1402px"><div class="ico"><svg width="52" height="52" viewBox="0 0 52 52" fill="none" stroke="#1e73c8" stroke-width="2"><rect x="20" y="6" width="26" height="34"/><path d="M25 14h16M25 20h16M25 26h10"/><circle cx="14" cy="32" r="9"/><rect x="6" y="42" width="24" height="6"/><path d="M42 30l6 6-10 10h-6v-6z"/></svg></div><h3>Financial gains</h3><p>Financial gains through reduced write-offs and right-sized care</p></div>

<svg class="abs" style="left:0;top:1670px" width="1200" height="760" viewBox="0 0 1200 760" preserveAspectRatio="none">
  <path d="M0 40 C300 140 700 -40 1000 10 C1100 25 1160 60 1200 100 L1200 640 C1100 590 960 570 800 585 C550 610 250 700 0 670 Z" fill="#f2f2f2"/>
</svg>

<h2 class="section-title abs" style="top:1809px">CLINICAL <span>EVIDENCE</span></h2>
<div class="card abs" style="left:111px;top:1890px"><div class="img" style="background:linear-gradient(135deg,#4b8fd0,#9fb6c9)" role="img" aria-label="Photo of a clinician holding a phone with AI health icons"></div><h4>AI power saves time and improves treatment plan quality</h4><div class="meta">▦ Dec 10, 2020 &nbsp;|&nbsp; ● Dana Reyes</div><div class="dl"><svg width="12" height="14" viewBox="0 0 12 14" fill="none" stroke="#1e73c8" stroke-width="1.3"><path d="M1 1h7l3 3v9H1z"/></svg>DownLoad Now</div></div>
<div class="card abs" style="left:443px;top:1890px"><div class="img" style="background:linear-gradient(135deg,#6f86a6,#c6d3e2)" role="img" aria-label="Photo of a doctor holding a folder in front of medical screens"></div><h4>Leveraging Artificial Intelligence (AI) clinical decision support</h4><div class="meta">▦ Dec 10, 2020 &nbsp;|&nbsp; ● Dana Reyes</div><div class="dl"><svg width="12" height="14" viewBox="0 0 12 14" fill="none" stroke="#1e73c8" stroke-width="1.3"><path d="M1 1h7l3 3v9H1z"/></svg>DownLoad Now</div></div>
<div class="card abs" style="left:775px;top:1890px"><div class="img" style="background:linear-gradient(135deg,#7fa7c7,#3f7aa8)" role="img" aria-label="Photo of surgeons reviewing scans in an operating room"></div><h4>Implementation and impact of AI decision support software</h4><div class="meta">▦ Dec 10, 2020 &nbsp;|&nbsp; ● Dana Reyes</div><div class="dl"><svg width="12" height="14" viewBox="0 0 12 14" fill="none" stroke="#1e73c8" stroke-width="1.3"><path d="M1 1h7l3 3v9H1z"/></svg>DownLoad Now</div></div>

<h2 class="section-title abs" style="top:2464px">OUR <span>PARTNERS</span></h2>
<svg class="abs" style="left:46px;top:2594px" width="18" height="30" viewBox="0 0 18 30"><path d="M15 2L3 15l12 13" stroke="#222" stroke-width="2.5" fill="none"/></svg>
<svg class="abs" style="left:1136px;top:2594px" width="18" height="30" viewBox="0 0 18 30"><path d="M3 2l12 13L3 28" stroke="#222" stroke-width="2.5" fill="none"/></svg>
<div class="partner abs" style="left:110px;top:2552px"><div class="badge" style="background:#4a2a7a"></div></div>
<div class="partner abs" style="left:357px;top:2552px"><div class="badge" style="background:#b21f5a"></div></div>
<div class="partner abs" style="left:604px;top:2552px"><div class="badge" style="background:#12305a;width:90px"></div></div>
<div class="partner abs" style="left:851px;top:2552px"><div class="badge" style="background:#1d4f91"></div></div>

<section class="contact abs">
  <h2>Contact Us</h2>
  <div class="c-item" style="left:80px"><div class="ico"><svg width="18" height="24" viewBox="0 0 18 24"><path d="M9 0a9 9 0 019 9c0 6-9 15-9 15S0 15 0 9a9 9 0 019-9z" fill="#fff"/><circle cx="9" cy="9" r="3.5" fill="#2aa0e4"/></svg></div><h5>California Address</h5><p>2180 Harbor View Road, Suite<br>310Alderton, CA 94011</p></div>
  <div class="c-item" style="left:341px"><div class="ico"><svg width="18" height="24" viewBox="0 0 18 24"><path d="M9 0a9 9 0 019 9c0 6-9 15-9 15S0 15 0 9a9 9 0 019-9z" fill="#fff"/><circle cx="9" cy="9" r="3.5" fill="#2aa0e4"/></svg></div><h5>Boston Address</h5><p>17 Quarry Lane Second Floor<br>Millbrook, MA 01960</p></div>
  <div class="c-item" style="left:603px"><div class="ico"><svg width="20" height="20" viewBox="0 0 20 20"><path d="M4 1l4 4-2 3c1 3 3 5 6 6l3-2 4 4-3 3C8 19 1 12 1 4z" fill="#fff"/></svg></div><h5>Phone</h5><p>(555) 010-4179</p></div>
  <div class="c-item" style="left:863px"><div class="ico"><svg width="20" height="16" viewBox="0 0 20 16"><rect width="20" height="16" rx="2" fill="#fff"/><path d="M1 2l9 7 9-7" stroke="#2aa0e4" stroke-width="1.8" fill="none"/></svg></div><h5>Email</h5><p>info@talvex-health.example<br>support@talvex-health.example</p></div>
</section>

<footer class="footer">
  <div class="logo abs">Talvex Health <span class="dot"></span></div>
  <div class="socials abs"><span></span><span></span><span></span><span></span></div>
  <div class="fcol abs" style="left:415px;top:3138px">
    <h6>Our Office Address</h6>
    <div class="finfo"><svg width="12" height="12" viewBox="0 0 20 20"><path d="M4 1l4 4-2 3c1 3 3 5 6 6l3-2 4 4-3 3C8 19 1 12 1 4z" fill="#1e73c8"/></svg><b>Phone</b>(555) 010-4179</div>
    <div class="finfo"><svg width="14" height="11" viewBox="0 0 20 16"><rect width="20" height="16" rx="2" fill="#1e73c8"/><path d="M1 2l9 7 9-7" stroke="#fff" stroke-width="1.8" fill="none"/></svg><b>Email</b>info@talvex-health.example</div>
    <div class="finfo"><svg width="10" height="14" viewBox="0 0 18 24"><path d="M9 0a9 9 0 019 9c0 6-9 15-9 15S0 15 0 9a9 9 0 019-9z" fill="#1e73c8"/></svg><b>Location</b>2180 Harbor View Road Suite 310<br>Alderton, CA 94011</div>
  </div>
  <div class="fcol abs" style="left:755px;top:3138px"><h6>Company</h6><a>Home</a><a>Solutions</a><a>Clinical Evidence</a><a>&nbsp;About</a><a>Contact Us</a></div>
  <div class="fcol abs" style="left:965px;top:3136px"><h6>Information</h6><a>Terms &amp; Conditions</a><a>Privacy Policy</a><a>Disclaimer</a><a>Site Map</a><a>Customer Support</a></div>
  <div class="divider abs"></div>
  <p class="copy abs">Copyrights ©talvex-health 2020 | Allrights Reserved</p>
</footer>

</body>
</html>
```